Business card design Needed for new logo / Construction business, home extensions and new builds

We need a business card design using our new logo files which i will attach to this project :)

We are a small construction business specialising in home extensions, new builds and property development. We are very ambitious and would appreciate professional and elegant designs for our new business card.

Very serious about using the services on MakerQuarry and recently acquired our new logo from here :)

Please get involved, i will feedback when i can as i am very busy but can respond daily, thanks

Target Market(s)

People that want to build onto their houses, new building developments or adding too their existing property

Industry/Entity Type

Construction

Contact Information for Business Card

Renwick Tolliver Construction, Lionel Ashby (Managing Director), Tel 07822254961, email - info@renwick-tolliver, www.renwick-tolliver.co.uk

Colors

Designer to choose colors to be used in the design.

Requirements
Must have
• I like a deep grey on the back please. A lot of you have provided black from and back, try mixing things up a little. The black looks cool 😎 Thanks

```html
<!DOCTYPE html>
<html lang="en">
<head>
<meta charset="utf-8">
<title>Renwick Tolliver Construction – Business Card</title>
<link href="https://fonts.googleapis.com/css2?family=Cinzel:wght@600&family=Poppins:wght@400;500&display=swap" rel="stylesheet">
<style>
  :root {
    --backdrop: #1e1e1e;
    --card: #050505;
    --back-grey: #3a3a3c;
    --back-grey-deep: #2a2a2c;
    --gold: #d9a52b;
    --gold-light: #f3d27a;
    --gold-dark: #9a6b12;
    --silver: #e6e6e6;
    --silver-dark: #8c8c8c;
    --white: #f4f4f4;
  }
  * { margin: 0; padding: 0; box-sizing: border-box; }
  html, body { width: 1200px; height: 866px; overflow: hidden; }
  body {
    background: var(--backdrop);
    font-family: "Poppins", sans-serif;
    position: relative;
  }
  .card {
    position: absolute;
    left: 290px;
    width: 620px;
    height: 355px;
    box-shadow: 0 14px 30px rgba(0,0,0,.6);
    overflow: hidden;
  }
  .card--back {
    top: 48px;
    background: radial-gradient(ellipse at 50% 40%, var(--back-grey) 0%, var(--back-grey-deep) 80%);
  }
  .card--front {
    top: 463px;
    background: radial-gradient(ellipse at 40% 35%, #151515 0%, var(--card) 70%);
  }

  .brand {
    position: absolute;
    font-family: "Cinzel", serif;
    font-weight: 600;
    color: var(--gold);
    text-align: center;
    line-height: 1.15;
  }
  .brand__mark {
    display: block;
    margin: 0 auto 12px;
    background: var(--gold);
  }
  .card--back .brand {
    left: 0; right: 0; top: 108px;
    font-size: 34px;
    letter-spacing: 2px;
  }
  .card--back .brand__mark { width: 26px; height: 26px; }
  .card--back .brand__sub { font-size: 24px; letter-spacing: 4px; }

  .card--front .brand {
    right: 40px; top: 122px;
    font-size: 22px;
    letter-spacing: 1.5px;
  }
  .card--front .brand__mark { width: 18px; height: 18px; margin-bottom: 8px; }
  .card--front .brand__sub { font-size: 16px; letter-spacing: 3px; }

  .person { position: absolute; left: 40px; top: 36px; }
  .person__name {
    font-family: "Cinzel", serif;
    font-weight: 600;
    font-size: 21px;
    letter-spacing: 1.5px;
    color: var(--white);
  }
  .person__title {
    font-size: 14px;
    color: var(--gold);
    letter-spacing: .5px;
  }
  .rule {
    position: absolute;
    height: 1px;
    background: var(--gold);
  }
  .rule--top { left: 40px; top: 100px; width: 250px; }
  .rule--address { left: 330px; right: 40px; top: 235px; }

  .contact {
    position: absolute; left: 40px; top: 112px;
    list-style: none;
    font-size: 14px;
    color: var(--white);
    line-height: 1.7;
  }
  .contact li { display: flex; align-items: center; gap: 8px; }
  .contact svg { width: 14px; height: 14px; fill: var(--gold); }

  .address {
    position: absolute; right: 40px; top: 245px;
    font-size: 13px;
    color: var(--white);
    text-align: right;
    line-height: 1.5;
  }
  .band { position: absolute; left: 0; bottom: 0; width: 620px; height: 60px; }
  .band__web {
    position: absolute; right: 40px; bottom: 11px;
    font-size: 15px;
    font-weight: 500;
    color: var(--white);
    letter-spacing: .5px;
  }
</style>
</head>
<body>

<section class="card card--back" aria-label="Card back">
  <div class="brand">
    <span class="brand__mark"></span>
    <span class="brand__name">Renwick Tolliver</span><br>
    <span class="brand__sub">Construction</span>
  </div>
</section>

<section class="card card--front" aria-label="Card front">
  <div class="person">
    <p class="person__name">LIONEL ASHBY</p>
    <p class="person__title">Managing Director</p>
  </div>
  <div class="rule rule--top"></div>
  <ul class="contact">
    <li>
      <svg viewBox="0 0 24 24"><path d="M6.6 10.8a15.1 15.1 0 0 0 6.6 6.6l2.2-2.2a1 1 0 0 1 1-.25 11.4 11.4 0 0 0 3.6.57 1 1 0 0 1 1 1V20a1 1 0 0 1-1 1A17 17 0 0 1 3 4a1 1 0 0 1 1-1h3.5a1 1 0 0 1 1 1c0 1.25.2 2.45.57 3.6a1 1 0 0 1-.25 1z"/></svg>
      07822254961
    </li>
    <li>
      <svg viewBox="0 0 24 24"><path d="M2 5h20v14H2zm2 2v.5l8 5 8-5V7zm0 2.8V17h16V9.8l-8 5z"/></svg>
      info@renwick-tolliver.co.uk
    </li>
  </ul>

  <div class="brand">
    <span class="brand__mark"></span>
    <span class="brand__name">Renwick Tolliver</span><br>
    <span class="brand__sub">Construction</span>
  </div>

  <div class="rule rule--address"></div>
  <p class="address">18, Harrowgate Lane<br>Leeds LS6 2QT</p>

  <svg class="band" viewBox="0 0 620 60" preserveAspectRatio="none" aria-hidden="true">
    <defs>
      <linearGradient id="goldBand" x1="0" y1="0" x2="0" y2="1">
        <stop offset="0" stop-color="#f3d27a"/>
        <stop offset=".5" stop-color="#d9a52b"/>
        <stop offset="1" stop-color="#9a6b12"/>
      </linearGradient>
      <linearGradient id="silverLine" x1="0" y1="0" x2="1" y2="0">
        <stop offset="0" stop-color="#e6e6e6"/>
        <stop offset="1" stop-color="#8c8c8c"/>
      </linearGradient>
    </defs>
    <rect x="0" y="22" width="250" height="4" fill="url(#silverLine)"/>
    <rect x="0" y="28" width="250" height="2" fill="#9a6b12"/>
    <path d="M235 60 C255 60 250 22 285 22 L620 22 L620 60 Z" fill="url(#goldBand)"/>
  </svg>
  <p class="band__web">www.renwick-tolliver.co.uk</p>
</section>

</body>
</html>
```